Holistic/ Sports Psychologist needs flyer design

I need a flyer designed that catches the attention of potential customers - (parents of young athletes and athletes) who may be looking for psychological services. I have a logo and all the relevant info for the flyer but would like someone to take it and make it look creative, fun, fresh and attention getting for high school and college athletes. The colors used can be from my logo design which represents my holistic approach.
Target Market(s)
high school and collegiate athletes
Industry/Entity Type
sports psychology
Requirements
Must have
- Info I put on the flyer with my logo and please add some graphics and color based on my logo

```html
<!DOCTYPE html>
<html lang="en">
<head>
<meta charset="utf-8">
<title>Dr. Rosalind Avery – Holistic and Sports Psychology Consulting</title>
<link href="https://fonts.googleapis.com/css2?family=Itim&family=Poppins:wght@400;500;600;700&display=swap" rel="stylesheet">
<style>
:root{
  --navy:#13325e;
  --navy-mid:#1f4a80;
  --blue:#2d5f9e;
  --ring:#2f5f9c;
  --green:#8dc363;
  --green-dark:#5b8a2f;
  --purple:#5940a6;
  --ink:#1d1d1d;
  --muted:#444;
  --white:#ffffff;
}
*{margin:0;padding:0;box-sizing:border-box}
html,body{width:960px;height:1200px;overflow:hidden;background:var(--white)}
body{font-family:"Poppins",sans-serif;color:var(--ink);position:relative}
.flyer{position:absolute;inset:0;width:960px;height:1200px;overflow:hidden;background:var(--white)}
.header-art{position:absolute;left:0;top:0}
.brand{position:absolute;left:70px;top:52px;display:flex;align-items:center;gap:14px}
.brand-mark{width:90px;height:90px;border-radius:50%;background:var(--white);border:5px solid var(--blue)}
.brand-name{font-family:"Itim",cursive;font-size:25px;color:var(--white);padding-bottom:6px;border-bottom:18px solid var(--green);padding-right:30px;line-height:1.2;margin-top:20px}
.hero-title{position:absolute;left:70px;top:168px;font-family:"Itim",cursive;font-size:55px;line-height:57px;color:var(--white);font-weight:400}
.hero-title .accent{color:var(--green)}
.section-heading{position:absolute;left:70px;top:478px;font-size:25.5px;font-weight:700;line-height:33px;color:var(--blue)}
.section-heading .accent{color:var(--green)}
.services{position:absolute;left:42px;top:580px;display:grid;grid-template-columns:140px 186px 140px 212px 170px;width:850px}
.service{text-align:center;padding:0 4px;border-right:1px dotted #777;min-height:235px}
.service:last-child{border-right:none}
.service-icon{width:56px;height:56px;border-radius:50%;background:var(--blue);border:3px solid var(--green);margin:0 auto 10px}
.service-title{font-size:18.5px;font-weight:600;line-height:22px;color:var(--purple);margin-bottom:6px}
.service-text{font-size:12.2px;line-height:14.8px;color:var(--ink)}
.divider{position:absolute;left:0;right:0;top:845px;height:1px;background:#dcdcdc}
.portrait{position:absolute;left:46px;top:892px;width:206px;height:206px;border-radius:50%;border:4px solid var(--ring);background:linear-gradient(160deg,#8fa3b3 0%,#58708a 45%,#2a3a6c 100%)}
.bio{position:absolute;left:406px;top:860px;width:520px}
.bio-name{font-family:"Itim",cursive;font-size:40px;color:var(--green-dark);line-height:46px;margin-bottom:14px;margin-left:-4px}
.bio-text{font-size:11.3px;line-height:14.8px;color:var(--muted);letter-spacing:.15px}
.bio-text + .bio-text{margin-top:14px}
.bio-text .label{color:var(--purple)}
.facts{position:absolute;left:404px;top:1052px;display:flex;gap:60px;align-items:center}
.fact{display:flex;align-items:center;gap:22px}
.fact-text{font-size:16px;font-weight:600;line-height:19px;color:var(--ink)}
.fact-text .accent{color:var(--purple)}
.footer{position:absolute;left:0;right:0;top:1123px;height:77px;background:linear-gradient(90deg,#8cc267 0%,#6fa394 45%,#3f6f9f 100%);display:flex;align-items:center;padding-left:66px;color:var(--white);font-weight:500}
.footer-item{display:flex;align-items:center;gap:10px}
.footer-sep{width:1px;height:36px;background:rgba(255,255,255,.45);margin:0 24px}
.footer-dot{width:24px;height:24px;border-radius:50%;background:var(--purple);display:flex;align-items:center;justify-content:center;flex:none}
.phone{font-size:24px;font-weight:600;letter-spacing:.5px}
.address{font-size:15px;line-height:19px}
.web{font-size:16px}
</style>
</head>
<body>
<main class="flyer">

  <svg class="header-art" width="960" height="600" viewBox="0 0 960 600">
    <defs>
      <linearGradient id="navyFill" x1="0" y1="1" x2="1" y2="0">
        <stop offset="0" stop-color="#2f5f96"/>
        <stop offset=".55" stop-color="#173a6b"/>
        <stop offset="1" stop-color="#0f2a52"/>
      </linearGradient>
      <linearGradient id="photoTones" x1="0" y1="0" x2="1" y2="1">
        <stop offset="0" stop-color="#4f8a34"/>
        <stop offset=".45" stop-color="#9cbf8a"/>
        <stop offset=".7" stop-color="#7fb0d6"/>
        <stop offset="1" stop-color="#d8c4a3"/>
      </linearGradient>
    </defs>
    <path class="header-band" d="M0,0 H680 C700,150 650,330 560,395 C470,450 300,475 0,415 Z" fill="url(#navyFill)"/>
    <path class="header-swoosh" d="M705,-5 C730,140 690,320 580,395 C490,455 360,478 270,475" fill="none" stroke="var(--green)" stroke-width="9"/>
    <circle cx="730" cy="252" r="212" fill="#ffffff"/>
    <circle cx="730" cy="252" r="203" fill="none" stroke="var(--ring)" stroke-width="5"/>
    <circle cx="730" cy="252" r="192" fill="url(#photoTones)" role="img" aria-label="Collage of sports gear on grass, a young woman looking out at the sea, and a group of cheering young athletes"/>
  </svg>

  <div class="brand">
    <div class="brand-mark"></div>
    <div class="brand-name">Dr. Rosalind Avery</div>
  </div>

  <h1 class="hero-title">Holistic<br>Psychology and<br><span class="accent">Sports Psychology<br>Consulting</span></h1>

  <h2 class="section-heading">Ways to Improve Athletic Performance Using Sports<br><span class="accent">and Holistic Psychology</span></h2>

  <section class="services">
    <article class="service">
      <div class="service-icon"></div>
      <h3 class="service-title">Mental<br>Skills<br>Training</h3>
      <p class="service-text">Ex: visualization, goal-setting, motivation, self- talk, mindset, concentration techniques</p>
    </article>
    <article class="service">
      <div class="service-icon"></div>
      <h3 class="service-title">Performance<br>Enhancement</h3>
      <p class="service-text">Eliminate psychological barriers that are hindering performance such as self- doubt, perfectionism, fear of failure, and burnout</p>
    </article>
    <article class="service">
      <div class="service-icon"></div>
      <h3 class="service-title">Mental<br>Health</h3>
      <p class="service-text">Anxiety and stress management by using things such as relaxation techniques, breathwork, and mindfulness practices</p>
    </article>
    <article class="service">
      <div class="service-icon"></div>
      <h3 class="service-title">Injury Recovery<br>Support</h3>
      <p class="service-text">Assist athletes in maintain resilience and positive mental attitude during rehabilitation as well as processing emotions relating to any potential trauma caused by the injury or life transitions resulting from it.</p>
    </article>
    <article class="service">
      <div class="service-icon"></div>
      <h3 class="service-title">Burnout<br>prevention</h3>
      <p class="service-text">Teach athletes how to have balance in sports and life so they can experience longevity in their sports as well asoverall optimal health and well-being.</p>
    </article>
  </section>

  <div class="divider"></div>

  <div class="portrait" role="img" aria-label="Portrait photo of the psychologist seated on a rocky shoreline"></div>

  <section class="bio">
    <h2 class="bio-name">Dr. Rosalind Avery</h2>
    <p class="bio-text">Dr. Rosalind Avery is a licensed psychologist. She understands the unique experiences of athletes due to her background as an All- American swimmer, collegiate and age group swim coach, parent of a collegiate/professional athlete, and sports psychology researcher. She works with athletes to optimize performance and overall well-being.</p>
    <p class="bio-text"><span class="label">Her specializations include:</span> performance anxiety, mental performance,Stress management, anxiety, depressions, trauma, life transitions,relationship issues, injury, and sleep.</p>
  </section>

  <div class="facts">
    <div class="fact">
      <p class="fact-text">All services are provided<br><span class="accent">online via telehealth.</span></p>
      <svg width="50" height="46" viewBox="0 0 50 46" aria-hidden="true" fill="none" stroke="var(--blue)" stroke-width="2">
        <rect x="3" y="6" width="44" height="30" rx="2"/>
        <line x1="25" y1="36" x2="25" y2="42"/>
        <line x1="16" y1="43" x2="34" y2="43"/>
        <circle cx="25" cy="17" r="5"/>
        <path d="M15 32c1-6 5-8 10-8s9 2 10 8"/>
      </svg>
    </div>
    <div class="fact">
      <p class="fact-text">Sessions are<br><span class="accent">30 or 55 minutes.</span></p>
      <svg width="48" height="48" viewBox="0 0 48 48" aria-hidden="true" fill="none" stroke="var(--blue)" stroke-width="2.2" style="margin-left:-12px">
        <circle cx="24" cy="24" r="21"/>
        <polyline points="24,11 24,24 32,30"/>
      </svg>
    </div>
  </div>

  <footer class="footer">
    <div class="footer-item">
      <span class="footer-dot">
        <svg width="13" height="13" viewBox="0 0 24 24" fill="#fff" aria-hidden="true"><path d="M6.6 10.8a15 15 0 0 0 6.6 6.6l2.2-2.2c.3-.3.7-.4 1-.2 1.1.4 2.3.6 3.6.6.6 0 1 .4 1 1V20c0 .6-.4 1-1 1A17 17 0 0 1 3 4c0-.6.4-1 1-1h3.5c.6 0 1 .4 1 1 0 1.3.2 2.5.6 3.6.1.3 0 .7-.2 1z"/></svg>
      </span>
      <span class="phone">904-555-0187</span>
    </div>
    <div class="footer-sep"></div>
    <div class="footer-item">
      <span class="footer-dot">
        <svg width="12" height="14" viewBox="0 0 24 28" fill="#fff" aria-hidden="true"><path d="M12 0a9 9 0 0 0-9 9c0 7 9 17 9 17s9-10 9-17a9 9 0 0 0-9-9zm0 12.5A3.5 3.5 0 1 1 12 5.5a3.5 3.5 0 0 1 0 7z"/></svg>
      </span>
      <span class="address">2280 Harbor Lane #310<br>Seabrook Beach, FL 32099</span>
    </div>
    <div class="footer-sep"></div>
    <div class="footer-item">
      <span class="footer-dot">
        <svg width="14" height="14" viewBox="0 0 24 24" fill="none" stroke="#fff" stroke-width="2" aria-hidden="true"><circle cx="12" cy="12" r="10"/><ellipse cx="12" cy="12" rx="4" ry="10"/><line x1="2" y1="12" x2="22" y2="12"/></svg>
      </span>
      <span class="web">www.drrosalindavery.com</span>
    </div>
  </footer>

</main>
</body>
</html>
```